Business Card for brovaLINK

Create a Business Card with an existing logo for brovaLINK AG. We are a Information Technology company that does consulting and developing SW to automate business processes. The main colors are given from the logo.

Industry/Entity Type

Business

Requirements
Nice to have
• we use a a font style Century Gothic in our documents

```html
<!DOCTYPE html>
<html lang="en">
<head>
<meta charset="utf-8">
<title>brovaLINK AG – Business Card</title>
<link href="https://fonts.googleapis.com/css2?family=Didact+Gothic&display=swap" rel="stylesheet">
<style>
  :root {
    --bg: #ece9e4;
    --white: #ffffff;
    --ink-grey: #4a4d52;
    --blue-deep: #1d3a9a;
    --blue-mid: #1f6fd0;
    --blue-light: #27a6e6;
    --green: #3db34a;
    --green-light: #9bd33a;
    --lime: #c6e03a;
    --shadow: rgba(20, 30, 60, 0.22);
  }
  * { box-sizing: border-box; margin: 0; padding: 0; }
  html, body {
    width: 1200px; height: 1024px; overflow: hidden;
    background: var(--bg);
    font-family: "Didact Gothic", "Century Gothic", sans-serif;
  }
  .sheet { position: relative; width: 1200px; height: 1024px; }

  .card {
    position: absolute; left: 280px;
    width: 640px; height: 390px;
    border-radius: 26px; overflow: hidden;
    box-shadow: 0 14px 30px var(--shadow);
  }
  .card--front { top: 90px; background: var(--white); }
  .card--back {
    top: 545px;
    background: linear-gradient(115deg, var(--blue-mid) 0%, var(--blue-light) 45%, var(--blue-mid) 75%, var(--blue-deep) 100%);
  }
  .card__art { position: absolute; inset: 0; width: 100%; height: 100%; }

  /* front */
  .brand {
    position: absolute; left: 40px; top: 150px;
    display: flex; align-items: center; gap: 14px;
  }
  .brand__dot {
    width: 44px; height: 44px; border-radius: 50%;
    background: var(--blue-mid);
  }
  .brand__name { font-size: 46px; color: var(--ink-grey); letter-spacing: -0.5px; }

  .person { position: absolute; right: 34px; top: 38px; text-align: right; color: var(--white); }
  .person__name { color: var(--green-light); font-size: 22px; font-weight: 700; }
  .person__role { font-size: 15px; margin-top: 2px; }

  .contact { position: absolute; right: 34px; top: 112px; list-style: none; color: var(--white); font-size: 16px; line-height: 27px; text-align: right; }
  .contact li { display: flex; justify-content: flex-end; align-items: center; gap: 10px; }
  .contact svg { width: 13px; height: 13px; flex: none; }

  .address { position: absolute; left: 290px; bottom: 38px; color: var(--white); font-size: 17px; line-height: 24px; display: flex; gap: 8px; }
  .address svg { width: 14px; height: 18px; margin-top: 3px; flex: none; }

  /* back */
  .back-brand {
    position: absolute; left: 0; right: 0; top: 130px;
    display: flex; justify-content: center; align-items: center; gap: 20px;
  }
  .back-brand__dot { width: 58px; height: 58px; border-radius: 50%; background: var(--white); }
  .back-brand__name { font-size: 78px; color: var(--white); letter-spacing: -1px; }
  .back-url { position: absolute; left: 0; right: 0; top: 268px; text-align: center; color: var(--white); font-size: 20px; letter-spacing: 0.5px; }
</style>
</head>
<body>
<main class="sheet">

  <section class="card card--front" aria-label="Business card front">
    <svg class="card__art" viewBox="0 0 640 390" preserveAspectRatio="none" aria-hidden="true">
      <defs>
        <linearGradient id="frontBlue" x1="0" y1="0" x2="1" y2="1">
          <stop offset="0" stop-color="#1f6fd0"/>
          <stop offset="0.55" stop-color="#27a6e6"/>
          <stop offset="1" stop-color="#1d3a9a"/>
        </linearGradient>
        <linearGradient id="frontGreen" x1="0" y1="0" x2="0" y2="1">
          <stop offset="0" stop-color="#9bd33a"/>
          <stop offset="1" stop-color="#3db34a"/>
        </linearGradient>
      </defs>
      <path class="band-green" d="M300 0 C330 140 300 300 230 390 L640 390 L640 0 Z" fill="url(#frontGreen)"/>
      <path class="band-white" d="M318 0 C345 140 318 300 252 390 L640 390 L640 0 Z" fill="#ffffff"/>
      <path class="band-blue" d="M330 0 C358 140 332 300 266 390 L640 390 L640 0 Z" fill="url(#frontBlue)"/>
    </svg>

    <div class="brand">
      <span class="brand__dot"></span>
      <span class="brand__name">brovaLINK</span>
    </div>

    <div class="person">
      <div class="person__name">Lukas Brandt</div>
      <div class="person__role">CEO</div>
    </div>

    <ul class="contact">
      <li>+41 56 410 28 63
        <svg viewBox="0 0 16 16"><rect x="2" y="3" width="12" height="10" rx="2" fill="#9bd33a"/></svg></li>
      <li>+41 79 352 47 19
        <svg viewBox="0 0 16 16"><path d="M4 1 L7 5 L5 7 C6 9 7 10 9 11 L11 9 L15 12 L13 15 C7 15 1 9 1 3 Z" fill="#9bd33a"/></svg></li>
      <li>lukas.brandt@brovalink.ch
        <svg viewBox="0 0 16 16"><rect x="1" y="3" width="14" height="10" rx="1" fill="#9bd33a"/><path d="M1 4 L8 9 L15 4" stroke="#1f6fd0" stroke-width="1.5" fill="none"/></svg></li>
      <li>www.brovalink.ch
        <svg viewBox="0 0 16 16"><circle cx="8" cy="8" r="6.5" fill="none" stroke="#9bd33a" stroke-width="2"/><path d="M1.5 8 H14.5 M8 1.5 V14.5" stroke="#9bd33a" stroke-width="1.3"/></svg></li>
    </ul>

    <div class="address">
      <svg viewBox="0 0 14 18"><path d="M7 0 C3 0 0 3 0 7 C0 12 7 18 7 18 C7 18 14 12 14 7 C14 3 11 0 7 0 Z" fill="#9bd33a"/><circle cx="7" cy="7" r="2.5" fill="#1f6fd0"/></svg>
      <span>Lindenweg 7, 5401 Musterdorf,<br>Switzerland</span>
    </div>
  </section>

  <section class="card card--back" aria-label="Business card back">
    <div class="back-brand">
      <span class="back-brand__dot"></span>
      <span class="back-brand__name">brovaLINK</span>
    </div>
    <div class="back-url">www.brovalink.ch</div>
  </section>

</main>
</body>
</html>
```